"Harbor Builders" is a residential building company and needs a new business card design and may re

We would like a redesign based on the existing logo, and would like to see a new font as well. We are bespoke home builders who build sustainable energy efficient homes.

Industry/Entity Type

Construction

Contact Information for Business Card

Business card size 40mm x 90mm

Colors

Designer to choose colors to be used in the design.

```html
<!DOCTYPE html>
<html lang="en">
<head>
<meta charset="utf-8">
<title>Harbor Builders – Business Card</title>
<link rel="stylesheet" href="https://fonts.googleapis.com/css2?family=Montserrat:wght@500;600;700&family=Open+Sans:wght@400;600;700&display=swap">
<style>
  :root {
    --backdrop: #141414;
    --card-white: #ffffff;
    --card-dark: #232323;
    --lime: #b5d334;
    --ink: #1a1a1a;
    --text-light: #e6e6e6;
  }
  * { box-sizing: border-box; margin: 0; padding: 0; }
  html, body {
    width: 1200px; height: 1000px; overflow: hidden;
    background: var(--backdrop);
  }
  .stage {
    position: relative; width: 1200px; height: 1000px;
    display: flex; align-items: center; justify-content: center; gap: 40px;
  }
  .card {
    position: relative; width: 500px; height: 285px; overflow: hidden;
    box-shadow: 0 10px 30px rgba(0,0,0,.5);
  }

  /* Front */
  .card-front {
    background: var(--card-white);
    display: flex; align-items: center; justify-content: center;
  }
  .brand {
    display: flex; align-items: center; gap: 10px;
    font-family: "Montserrat", sans-serif; font-weight: 600;
    color: var(--ink);
  }
  .brand-mark { width: 16px; height: 16px; background: var(--lime); flex: none; }
  .brand-front .brand-name { font-size: 30px; letter-spacing: 1px; }

  /* Back */
  .card-back { background: var(--card-dark); }
  .card-back .shapes { position: absolute; inset: 0; }
  .details {
    position: absolute; left: 30px; top: 34px;
    font-family: "Open Sans", sans-serif; color: var(--text-light);
  }
  .person-name {
    font-family: "Montserrat", sans-serif; font-weight: 600;
    font-size: 19px; color: #fff;
  }
  .person-name .surname { color: var(--lime); }
  .registration { font-size: 10.5px; margin-top: 2px; }
  .company {
    font-family: "Open Sans", sans-serif; font-weight: 700;
    font-size: 14px; color: var(--lime); margin-top: 14px;
  }
  .contact-list { list-style: none; margin-top: 12px; }
  .contact-list li {
    display: flex; align-items: center; gap: 8px;
    font-size: 11px; line-height: 17px;
  }
  .contact-list svg { width: 10px; height: 10px; flex: none; }
  .brand-back {
    position: absolute; left: 398px; top: 74px; width: 92px;
    flex-direction: column; gap: 6px; text-align: center;
  }
  .brand-back .brand-name { font-size: 14px; line-height: 16px; }
  .brand-back .brand-mark { width: 14px; height: 14px; }
  .address {
    position: absolute; right: 22px; bottom: 18px; text-align: right;
    font-family: "Open Sans", sans-serif; font-weight: 700; font-style: normal;
    font-size: 12px; line-height: 15px; color: var(--ink);
  }
</style>
</head>
<body>
<main class="stage">
  <section class="card card-front">
    <div class="brand brand-front">
      <span class="brand-mark"></span>
      <span class="brand-name">Harbor Builders</span>
    </div>
  </section>

  <section class="card card-back">
    <svg class="shapes" viewBox="0 0 500 285" preserveAspectRatio="none" aria-hidden="true">
      <polygon points="365,0 500,0 500,222 385,157" fill="#ffffff"/>
      <polygon points="260,285 385,157 500,222 500,285" fill="#b5d334"/>
    </svg>

    <div class="details">
      <p class="person-name">Daniel <span class="surname">Marsh</span></p>
      <p class="registration">Registration 40318 ABN: 51 204 778 312</p>
      <p class="company">Harbor Builders Pty Ltd</p>
      <ul class="contact-list">
        <li>
          <svg viewBox="0 0 10 10"><path d="M2 0.5 L3.8 2.8 L2.8 3.8 C3.5 5.3 4.7 6.5 6.2 7.2 L7.2 6.2 L9.5 8 L8.3 9.5 C4.3 9 1 5.7 0.5 1.7 Z" fill="#b5d334"/></svg>
          0400 123 987
        </li>
        <li>
          <svg viewBox="0 0 10 10"><rect x="0.5" y="2" width="9" height="6.5" fill="#b5d334"/><path d="M0.5 2 L5 5.5 L9.5 2" stroke="#232323" stroke-width="1" fill="none"/></svg>
          daniel@harborbuilders.com.au
        </li>
        <li>
          <svg viewBox="0 0 10 10"><circle cx="5" cy="5" r="4.3" fill="none" stroke="#b5d334" stroke-width="1.2"/><path d="M0.7 5 H9.3 M5 0.7 V9.3" stroke="#b5d334" stroke-width="1"/></svg>
          www.harborbuilders.com.au
        </li>
      </ul>
    </div>

    <div class="brand brand-back">
      <span class="brand-mark"></span>
      <span class="brand-name">Harbor<br>Builders</span>
    </div>

    <address class="address">
      PO Box 2207<br>Northgate LPO<br>Bayview, WA 6091
    </address>
  </section>
</main>
</body>
</html>
```